Redesign of business card for Cedar Ridge Mechanical

We are looking for a new design for our business cards for Cedar Ridge Mechanical. We are a plumbing & HVAC construction company, operating on the West Coast of Canada and USA. Logo attached.
Industry/Entity Type
Construction - Plumbing & HVAC
Contact Information for Business Card
Name, address, phone numbers, email, website address
Look and feel
Each slider illustrates characteristics of the customer's brand and the style your logo design should communicate.

```html
<!DOCTYPE html>
<html lang="en">
<head>
<meta charset="utf-8">
<title>Cedar Ridge Mechanical – Business Card</title>
<link rel="stylesheet" href="https://fonts.googleapis.com/css2?family=Montserrat:wght@400;500;700&display=swap">
<style>
  :root {
    --page-bg: #d9d4cc;
    --card-bg: #ece7df;
    --ink: #1e1d1c;
    --ink-soft: #2b2a28;
    --band: #151515;
    --contact-text: #cfc9c0;
  }
  html, body {
    margin: 0;
    padding: 0;
    width: 1200px;
    height: 1047px;
    overflow: hidden;
    background: var(--page-bg);
    font-family: "Montserrat", sans-serif;
  }
  .business-card {
    position: absolute;
    left: 80px;
    top: 233px;
    width: 1040px;
    height: 580px;
    border-radius: 26px;
    background: var(--card-bg);
    overflow: hidden;
    box-shadow: 0 18px 40px rgba(0,0,0,0.18);
  }
  .card-band {
    position: absolute;
    inset: 0;
    width: 100%;
    height: 100%;
  }
  .holder {
    position: absolute;
    left: 10px;
    top: 48px;
    display: flex;
    align-items: stretch;
    gap: 14px;
  }
  .holder-bar {
    width: 40px;
    background: var(--ink);
  }
  .holder-name {
    margin: 0;
    font-size: 34px;
    font-weight: 700;
    letter-spacing: 1px;
    color: var(--ink-soft);
    line-height: 1.1;
  }
  .holder-role {
    margin: 4px 0 0;
    font-size: 23px;
    font-weight: 500;
    color: var(--ink-soft);
  }
  .company-mark {
    position: absolute;
    right: 40px;
    top: 110px;
    display: flex;
    align-items: center;
    gap: 18px;
  }
  .company-square {
    width: 54px;
    height: 54px;
    background: var(--ink);
  }
  .company-name {
    font-size: 30px;
    font-weight: 700;
    letter-spacing: 1px;
    color: var(--ink);
    line-height: 1.15;
    text-transform: uppercase;
  }
  .contact {
    position: absolute;
    left: 45px;
    top: 300px;
    color: var(--contact-text);
    font-size: 23px;
    font-weight: 400;
  }
  .contact-address {
    margin: 0 0 36px;
    line-height: 1.45;
  }
  .contact-list {
    list-style: none;
    margin: 0;
    padding: 0;
  }
  .contact-list li {
    display: flex;
    align-items: center;
    gap: 8px;
    line-height: 1.4;
    margin-bottom: 4px;
  }
  .contact-icon {
    width: 20px;
    height: 20px;
    fill: none;
    stroke: var(--contact-text);
    stroke-width: 2;
  }
</style>
</head>
<body>
  <article class="business-card">
    <svg class="card-band" viewBox="0 0 1040 580" preserveAspectRatio="none" aria-hidden="true">
      <path fill="var(--band)" d="M0,235 C320,225 600,440 1040,450 L1040,580 L0,580 Z"/>
    </svg>

    <header class="holder">
      <div class="holder-bar"></div>
      <div>
        <h1 class="holder-name">DANIEL REYES</h1>
        <p class="holder-role">Managing Director</p>
      </div>
    </header>

    <div class="company-mark">
      <div class="company-square"></div>
      <div class="company-name">Cedar Ridge<br>Mechanical</div>
    </div>

    <section class="contact">
      <p class="contact-address">Your address, City<br>State, Zip 1234</p>
      <ul class="contact-list">
        <li>
          <svg class="contact-icon" viewBox="0 0 24 24" aria-hidden="true"><path d="M5 3h4l2 5-2.5 1.5a11 11 0 0 0 6 6L16 13l5 2v4a2 2 0 0 1-2 2A16 16 0 0 1 3 5a2 2 0 0 1 2-2z"/></svg>
          123 456 789
        </li>
        <li>
          <svg class="contact-icon" viewBox="0 0 24 24" aria-hidden="true"><rect x="3" y="5" width="18" height="14" rx="1"/><path d="M3 6l9 7 9-7"/></svg>
          info@yourgmail.com
        </li>
        <li>
          <svg class="contact-icon" viewBox="0 0 24 24" aria-hidden="true"><circle cx="12" cy="12" r="9"/><path d="M3 12h18M12 3c3 3 3 15 0 18M12 3c-3 3-3 15 0 18"/></svg>
          www.yourwebsite.com
        </li>
      </ul>
    </section>
  </article>
</body>
</html>
```